New business blog needs wordpress theme

I need a unique wordpress theme for my new business oriented blog at hollowpeakdesk.com. The blog focuses on my experience as an entrepreneur and offers insights into business problems while chronicling my experience building a new company.

I would like to see a theme that looks more like a creative professional's website, not a business website. Large photos, bright colors, unique layout. I do not want stock photos of people in suits doing business type things. Also, no pictures of me - I am blogging anonymously.

The design should communicate technology and beauty - for example, I really like the feel of the landing page at www.tundrelo.com - it is beautiful to look at but also reflects the cutting edge nature of what they are doing.

Industry/Entity Type

Business

```html
<!DOCTYPE html>
<html lang="en">
<head>
<meta charset="utf-8">
<title>Hollow Peak Desk</title>
<link rel="stylesheet" href="https://fonts.googleapis.com/css2?family=Varela+Round&family=Open+Sans:wght@400;600&display=swap">
<style>
:root{
  --orange:#f07c0a;
  --orange-dark:#e56a00;
  --orange-light:#f99a22;
  --teal:#2a8db0;
  --teal-dark:#1d7a9a;
  --text:#333;
  --muted:#666;
  --line:#dcdcdc;
  --footer:#1f1f1f;
}
*{box-sizing:border-box;margin:0;padding:0}
html,body{width:754px;height:1200px;overflow:hidden;background:#fff}
body{position:relative;font-family:'Open Sans',sans-serif;color:var(--text)}
.hero{position:absolute;left:0;top:0;width:754px;height:384px;
  background:radial-gradient(ellipse at 78% 40%,#5fa7d6 0%,#9ccbe9 28%,transparent 55%),
  linear-gradient(180deg,#cfe6f4 0%,#b7dbef 45%,#8ec3e4 75%,#e7f3fa 100%)}
.hero-line{position:absolute;top:0;left:0;width:754px;height:3px;background:#7fc0e0}
.brand{position:absolute;left:53px;top:20px;font-family:'Varela Round',sans-serif;font-size:27px;color:var(--orange)}
.tagline{position:absolute;left:54px;top:52px;font-size:7.5px;color:#4d5d68}
.search{position:absolute;left:527px;top:40px;width:174px;height:20px;border-radius:10px;background:#f2f6f8;font-size:8px;font-style:italic;color:#666;padding:5px 12px}
.nav{position:absolute;left:53px;top:74px;width:648px;height:34px;border-radius:2px;
  background:linear-gradient(180deg,var(--orange-light),var(--orange-dark));display:flex}
.nav a{color:#fff;text-decoration:none;font-size:11.5px;line-height:34px;padding:0 18px;border-right:1px solid #c95a00}
.slide-title{position:absolute;left:0;width:754px;top:190px;text-align:center;font-family:'Varela Round',sans-serif;font-size:27px;color:var(--teal-dark)}
.slide-sub{position:absolute;left:0;width:754px;top:222px;text-align:center;font-family:'Varela Round',sans-serif;font-size:17px;color:var(--orange)}
.arrow{position:absolute;top:200px}
.section-title{position:absolute;left:53px;top:409px;font-family:'Varela Round',sans-serif;font-size:18px;color:var(--teal)}
.post{position:absolute;left:53px;width:466px;height:150px;border:1px solid var(--line);background:linear-gradient(180deg,#fff 60%,#f4f4f4)}
.post-thumb{position:absolute;left:0;top:0;width:163px;height:148px}
.post-body{position:absolute;left:178px;top:12px;width:278px}
.post-title{font-family:'Varela Round',sans-serif;font-size:15.5px;color:#222;font-weight:400}
.post-author{font-size:8px;color:var(--teal);margin-top:4px}
.post-excerpt{font-size:7.6px;line-height:14px;color:var(--muted);margin-top:5px}
.post-meta{font-size:7.6px;color:var(--orange);margin-top:3px}
.widget{position:absolute;left:529px;width:172px;border:1px solid var(--line)}
.widget h3{font-family:'Varela Round',sans-serif;font-weight:400;font-size:13px;color:#fff;height:30px;line-height:30px;padding-left:13px}
.recent h3{background:linear-gradient(180deg,#3aa4c9,var(--teal-dark))}
.featured h3{background:linear-gradient(180deg,var(--orange-light),var(--orange-dark))}
.recent-item{padding:9px 13px;border-top:1px solid var(--line);font-size:7.4px;line-height:12px;color:#555}
.recent-item:first-of-type{border-top:none}
.recent-item b{display:block;color:#333;font-weight:600}
.topics{list-style:none;padding:6px 12px 14px}
.topics li{font-size:8px;color:#444;height:19px;line-height:19px;border-bottom:1px solid #e6e6e6;padding-left:12px;position:relative}
.topics li:last-child{border-bottom:none}
.topics li::before{content:"";position:absolute;left:3px;top:7px;border-left:3px solid #777;border-top:3px solid transparent;border-bottom:3px solid transparent}
.footer-rule{position:absolute;left:0;top:1117px;width:754px;height:4px;background:#e4e4e4}
.footer{position:absolute;left:0;top:1121px;width:754px;height:79px;background:var(--footer)}
.footer-links{position:absolute;left:57px;top:24px;font-size:9px;color:#fff}
.footer-links span{color:#888;margin:0 5px}
.copyright{position:absolute;left:57px;top:43px;font-size:7.5px;color:#666}
.social{position:absolute;left:612px;top:23px;display:flex;gap:3px}
.social i{width:19px;height:19px;border-radius:50%;background:#fff;display:block}
</style>
</head>
<body>
<header class="hero" role="img" aria-label="Bright blue photo of a desk globe beside a telephone">
  <div class="hero-line"></div>
</header>
<div class="brand">Hollow Peak Desk</div>
<div class="tagline">The author talks business. Best practices, articles and tips and about small business in the United States</div>
<div class="search">Search here</div>
<nav class="nav">
  <a>Home</a><a>Small Business</a><a>Technology</a><a>About the Author</a><a>Contact Us</a>
</nav>
<div class="slide-title">Cras a ante vitae enim iaculis aliquam mauris</div>
<div class="slide-sub">Phasellus felis dolor scelerisque a tempus</div>
<svg class="arrow" style="left:32px" width="42" height="42" viewBox="0 0 42 42"><circle cx="21" cy="21" r="20" fill="#fff"/><path d="M24 12 L16 21 L24 30" stroke="#333" stroke-width="1.5" fill="none"/></svg>
<svg class="arrow" style="left:680px" width="42" height="42" viewBox="0 0 42 42"><circle cx="21" cy="21" r="20" fill="#fff"/><path d="M18 12 L26 21 L18 30" stroke="#333" stroke-width="1.5" fill="none"/></svg>

<h2 class="section-title">LATEST BLOG</h2>

<article class="post" style="top:440px">
  <div class="post-thumb" role="img" aria-label="Photo looking up at glass office towers against a blue sky" style="background:linear-gradient(160deg,#2d4a6e,#6f9cc8 50%,#a9c6e2)"></div>
  <div class="post-body">
    <h4 class="post-title">Suspendisse vulputate aliquam dui</h4>
    <p class="post-author">by Author Name</p>
    <p class="post-excerpt">Phasellus felis dolor scelerisque a tempus eget lobortis id libero Aliquam nec erat at purus cursus interdum Vestibulum ligula augue bibendum accumsan vestibulum ut commodo a mi Morbi ornare gravida elit Integer congue augue et malesuada iaculis ipsum dui aliquet felis at cursus magna nisl nec elit Vestibulum gravida Praesent elementum</p>
    <p class="post-meta">Posted on 20 Jan, 2014 &nbsp;|&nbsp; 0 Comments &nbsp;|&nbsp; LEARN MORE</p>
  </div>
</article>
<article class="post" style="top:600px">
  <div class="post-thumb" role="img" aria-label="Chalk sketch of a light bulb framing a city skyline" style="background:radial-gradient(ellipse at 50% 40%,#b9c8d2,#4a4a4a 45%,#222)"></div>
  <div class="post-body">
    <h4 class="post-title">Morbi porta libero id ullamcorper non</h4>
    <p class="post-author">by Author Name</p>
    <p class="post-excerpt">Phasellus felis dolor scelerisque a tempus eget lobortis id libero Aliquam nec erat at purus cursus interdum Vestibulum ligula augue bibendum accumsan vestibulum ut commodo a mi Morbi ornare gravida elit Integer congue augue et malesuada iaculis ipsum dui aliquet felis at cursus magna nisl nec elit Vestibulum gravida Praesent elementum</p>
    <p class="post-meta">Posted on 20 Jan, 2014 &nbsp;|&nbsp; 0 Comments &nbsp;|&nbsp; LEARN MORE</p>
  </div>
</article>
<article class="post" style="top:761px">
  <div class="post-thumb" role="img" aria-label="Glass globe resting on printed financial charts" style="background:radial-gradient(circle at 60% 45%,#1d5ea8,#5d8fc7 30%,#d7dde4 55%,#eef0f2)"></div>
  <div class="post-body">
    <h4 class="post-title">Pellentesque faucibus accumsan ultricie</h4>
    <p class="post-author">by Author Name</p>
    <p class="post-excerpt">Phasellus felis dolor scelerisque a tempus eget lobortis id libero Aliquam nec erat at purus cursus interdum Vestibulum ligula augue bibendum accumsan vestibulum ut commodo a mi Morbi ornare gravida elit Integer congue augue et malesuada iaculis ipsum dui aliquet felis at cursus magna nisl nec elit Vestibulum gravida Praesent elementum</p>
    <p class="post-meta">Posted on 20 Jan, 2014 &nbsp;|&nbsp; 0 Comments &nbsp;|&nbsp; LEARN MORE</p>
  </div>
</article>
<article class="post" style="top:921px">
  <div class="post-thumb" role="img" aria-label="Hands using a tablet showing blue bar charts" style="background:linear-gradient(150deg,#eaf2f8,#b9d5ec 50%,#f1f4f7)"></div>
  <div class="post-body">
    <h4 class="post-title">Cras a ante vitae enim iaculis</h4>
    <p class="post-author">by Author Name</p>
    <p class="post-excerpt">Phasellus felis dolor scelerisque a tempus eget lobortis id libero Aliquam nec erat at purus cursus interdum Vestibulum ligula augue bibendum accumsan vestibulum ut commodo a mi Morbi ornare gravida elit Integer congue augue et malesuada iaculis ipsum dui aliquet felis at cursus magna nisl nec elit Vestibulum gravida Praesent elementum</p>
    <p class="post-meta">Posted on 20 Jan, 2014 &nbsp;|&nbsp; 0 Comments &nbsp;|&nbsp; LEARN MORE</p>
  </div>
</article>

<aside class="widget recent" style="top:405px">
  <h3>RECENT POSTS</h3>
  <div class="recent-item">Your friends are God's way of apologizing for your relatives.<b>Posted on 1st Oct, 2013</b></div>
  <div class="recent-item">The key is not to prioritize your schedule but to schedule your priorities.<b>Posted on 29 Sep, 2013</b></div>
  <div class="recent-item">Effective people are not problem-minded; they're opportunity-minded.<b>Posted on 28th Oct, 2013</b></div>
  <div class="recent-item">Far and away the best prize that life has to offer is the chance to work hard at work worth doing.<b>Posted on 27th Oct, 2013</b></div>
</aside>

<aside class="widget featured" style="top:671px">
  <h3>FEATURED TOPICS</h3>
  <ul class="topics">
    <li>Etiam eu urna Sed porta</li>
    <li>Suspendisse quam leo</li>
    <li>Molestie sed luctus</li>
    <li>Wuis feugiat pede</li>
    <li>Fusce tellus Sed metus</li>
    <li>Augue convallis</li>
    <li>Pulvinar eu ante</li>
  </ul>
</aside>

<div class="footer-rule"></div>
<footer class="footer">
  <div class="footer-links">Home<span>|</span>About<span>|</span>Small Business<span>|</span>Technology<span>|</span>Contact Us</div>
  <div class="copyright">© 2013 Company Name. &nbsp;All right reserved.</div>
  <div class="social"><i></i><i></i><i></i><i></i></div>
</footer>
</body>
</html>
```